Set up small scale company website

We need a website set up for our educational consultancy - Vexmore Education. We like the following site and want something similar www.plindarhub.co.uk We can provide the copy and images but need the following:- setting up the overall theme and design - to our requirements on colours and forma- Approximately 4 pages of services offered and with an index pageEtct (yellow and green)And the following pages - as well as a home page:- A contact page linked to our email addresses and registered business address 17 Wexbury Lane, Harwich, Essex, CO14 8PN- About Us page - An index of services page that links to between 4-6 pages outlining services- A News page that links to updates of latest services, events and activities - easily updated by usOn the homepage we'd like links to chirpnet and WorkLoop feeds and links to our other blogs and websites
Target Market(s)
Schools, local authoroties and multi-academy trusts
Logo Text
Vexmore Education
Coding
Coded - Design and coding required
Number of Pages Required
5+ page
Font styles to use
Requirements
Should not have
- No tacky pictures of mortar boards or chalk boards etc.

```html
<!DOCTYPE html>
<html lang="en">
<head>
<meta charset="utf-8">
<title>Vexmore Education</title>
<link href="https://fonts.googleapis.com/css2?family=Cinzel:wght@400;700&family=Ubuntu:wght@400;500;700&display=swap" rel="stylesheet">
<style>
:root{
  --green:#7ab51d;
  --green-dark:#5f9612;
  --green-light:#93cc2f;
  --yellow:#fbe82d;
  --ink:#1b1b1b;
  --text:#555;
  --muted:#999;
  --page:#f5f5f5;
  --white:#fff;
  --navy:#1e2433;
  --link:#1d6fb8;
}
*{margin:0;padding:0;box-sizing:border-box}
html,body{width:1200px;height:2571px;overflow:hidden}
body{position:relative;background:var(--page);font-family:"Ubuntu",sans-serif;color:var(--text)}
.abs{position:absolute}

.topbar{left:0;top:0;width:1200px;height:41px;background:var(--green);color:var(--white);font-size:15px}
.topbar .item{position:absolute;top:11px;display:flex;align-items:center;gap:10px}
.topbar .divider{position:absolute;left:851px;top:6px;width:1px;height:29px;background:rgba(255,255,255,.7)}

.header{left:0;top:41px;width:1200px;height:74px}
.logo{position:absolute;left:113px;top:22px;font-family:"Cinzel",serif;font-weight:700;font-size:26px;color:var(--ink);letter-spacing:.5px;white-space:nowrap}
.nav{position:absolute;top:29px;right:110px;display:flex;gap:38px;font-size:15px;color:var(--ink);align-items:center}

.hero{left:57px;top:115px;width:1087px;height:490px;overflow:hidden;background:linear-gradient(105deg,#6fa628 0%,#7ab51d 45%,#94cc36 100%)}
.hero-photo{position:absolute;left:0;top:0;width:470px;height:490px;background:linear-gradient(90deg,#8a6a4c 0%,#b79a7a 45%,#6f8f3a 100%)}
.hero-chevron{position:absolute;left:0;top:0}
.hero-title{position:absolute;left:503px;top:128px;font-family:"Cinzel",serif;font-size:44px;line-height:56px;color:var(--white);letter-spacing:.5px;white-space:nowrap}
.hero-text{position:absolute;left:512px;top:197px;width:520px;font-size:18px;line-height:25px;color:var(--white)}
.btn{display:flex;align-items:center;justify-content:center;border-radius:26px;font-weight:500;color:var(--ink);font-size:17px}
.hero .btn{position:absolute;left:509px;top:305px;width:190px;height:48px;background:var(--yellow);gap:9px;font-weight:700}

.dots{left:554px;top:633px;display:flex;gap:12px}
.dots span{width:14px;height:14px;border-radius:50%;border:2px solid var(--ink)}
.dots span.on{background:var(--ink)}

.welcome-title{left:0;top:733px;width:1200px;text-align:center;font-family:"Cinzel",serif;font-size:35px;font-weight:400;color:var(--ink);white-space:nowrap}
.welcome-title b{color:var(--green);font-weight:700}
.welcome-text{left:180px;top:800px;width:840px;text-align:center;font-size:14.5px;line-height:29px;color:var(--text)}
.welcome-actions{left:427px;top:960px;display:flex;gap:23px}
.welcome-actions .btn{height:48px}
.btn-green{width:157px;background:var(--green);color:var(--white)!important;font-weight:400!important}
.btn-yellow{width:166px;background:var(--yellow)}

.services{left:57px;top:1104px;width:1087px;height:547px;background:var(--green)}
.gear-badge{position:absolute;left:-12px;top:-12px;width:60px;height:60px;border-radius:50%;background:var(--white);display:flex;align-items:center;justify-content:center}
.services-title{position:absolute;left:54px;top:86px;font-family:"Cinzel",serif;font-size:37px;font-weight:400;color:var(--white);white-space:nowrap}
.services-title b{font-weight:700}
.services-lead{position:absolute;left:55px;top:134px;width:300px;font-size:15px;line-height:22px;color:var(--white)}
.service-list{position:absolute;left:56px;top:206px;width:327px;list-style:none}
.service-list li{height:54px;border-bottom:1px solid rgba(255,255,255,.75);display:flex;align-items:center;padding-left:27px;font-size:18px;font-weight:500;color:var(--white);position:relative}
.service-list li:first-child{border-top:1px solid rgba(255,255,255,.75)}
.service-list li.active{background:var(--yellow);color:var(--ink);height:46px;margin:0;border:none}
.service-list li.active::after{content:"";position:absolute;right:-21px;top:0;border-left:21px solid var(--yellow);border-top:23px solid transparent;border-bottom:23px solid transparent}

.service-card{position:absolute;left:450px;top:39px;width:580px;height:470px;background:var(--white);border-radius:3px;box-shadow:0 2px 8px rgba(0,0,0,.2)}
.service-photo{position:absolute;left:7px;top:7px;width:566px;height:262px;background:linear-gradient(180deg,#d8d2bf 0%,#b9b08f 30%,#6f8f48 60%,#58803a 100%)}
.service-icon{position:absolute;left:245px;top:233px;width:76px;height:48px;border-radius:38px 38px 0 0;background:var(--white);display:flex;justify-content:center;padding-top:10px}
.service-card h3{position:absolute;left:23px;top:300px;font-size:21px;font-weight:700;color:var(--ink)}
.service-card p{position:absolute;left:23px;top:338px;width:530px;font-size:15px;line-height:26px;color:var(--text)}
.service-card .more{position:absolute;left:23px;top:432px;font-size:13px;font-weight:700;color:var(--green-dark)}

.feed{top:1748px;height:369px;background:var(--white);border-radius:6px}
.feed-head{position:absolute;left:19px;top:16px;font-size:20px;color:var(--ink);display:flex;align-items:center;gap:8px}
.feed-head .sq{width:14px;height:14px;background:var(--link);border-radius:2px}
.post{position:absolute;left:17px;width:310px}
.post.faded{opacity:.5}
.avatar{position:absolute;left:0;top:0;width:40px;height:40px;border-radius:50%;background:linear-gradient(135deg,#c9b39a,#7d6a58)}
.post .name{position:absolute;left:56px;top:0;font-size:12px;color:var(--ink);font-weight:500}
.post .name span{color:var(--muted);font-weight:400;margin-left:14px}
.post .body{position:absolute;left:56px;top:20px;width:205px;font-size:11px;line-height:16px;color:var(--ink)}
.post .body a,.post .tag{color:var(--link);text-decoration:none}
.post .tag{position:absolute;left:56px;top:104px;font-size:11px}
.post .time{position:absolute;left:0;top:117px;font-size:9px;color:var(--ink)}
.post .dots3{position:absolute;right:10px;top:-8px;font-size:16px;color:var(--ink);letter-spacing:1px}
.stats-v{position:absolute;right:14px;top:16px;display:flex;flex-direction:column;align-items:center;gap:6px;font-size:8px;color:var(--muted)}
.stats-h{position:absolute;left:56px;top:117px;display:flex;gap:22px;font-size:9px;color:var(--muted);align-items:center}
.heart{color:#e0283c;font-size:14px}

.blog{position:absolute;left:14px;width:340px;height:92px}
.blog-thumb{position:absolute;left:0;top:0;width:86px;height:86px}
.blog h4{position:absolute;left:96px;top:0;font-size:18px;font-weight:700;color:var(--ink)}
.blog p{position:absolute;left:96px;top:27px;width:245px;font-size:12px;line-height:16px;color:#666}
.blog .date{position:absolute;left:96px;top:66px;font-size:10px;color:var(--ink);display:flex;align-items:center;gap:6px}
.blog .date i{width:8px;height:8px;background:var(--green);display:block}

.footer{left:0;top:2213px;width:1200px;height:358px;background:var(--navy)}
.phone-badge{position:absolute;left:572px;top:-27px;width:56px;height:56px;border-radius:50%;background:var(--white);display:flex;align-items:center;justify-content:center}
.social{position:absolute;left:485px;top:103px;display:flex;gap:9px}
.social span{width:50px;height:50px;border-radius:50%;border:2px solid var(--white);display:flex;align-items:center;justify-content:center}
.social span i{width:10px;height:10px;border-radius:50%;background:var(--white);display:block}
.contact-line{position:absolute;left:0;top:185px;width:1200px;display:flex;justify-content:center;align-items:center;gap:12px;font-size:14px;color:var(--white)}
.foot-nav{position:absolute;left:0;top:222px;width:1200px;text-align:center;font-size:16px;color:var(--white);word-spacing:2px}
.copyright{position:absolute;left:0;top:261px;width:1200px;text-align:center;font-size:14px;color:var(--white)}
</style>
</head>
<body>

<div class="abs topbar">
  <div class="item" style="left:689px">
    <svg width="15" height="15" viewBox="0 0 24 24"><path fill="#fff" d="M6.6 10.8a15 15 0 0 0 6.6 6.6l2.2-2.2c.3-.3.7-.4 1-.2 1.1.4 2.3.6 3.6.6.6 0 1 .4 1 1V20c0 .6-.4 1-1 1A17 17 0 0 1 3 4c0-.6.4-1 1-1h3.5c.6 0 1 .4 1 1 0 1.3.2 2.5.6 3.6.1.3 0 .7-.2 1z"/></svg>
    +142 600 3187
  </div>
  <div class="divider"></div>
  <div class="item" style="left:889px">
    <svg width="17" height="14" viewBox="0 0 24 18"><path fill="#fff" d="M0 0h24v2L12 10 0 2zM0 4.5l12 8 12-8V18H0z"/></svg>
    info@vexmore-edu.co.uk
  </div>
</div>

<header class="abs header">
  <div class="logo">Vexmore Education</div>
  <nav class="nav">
    <span>Home</span><span>Services</span><span>News</span><span>About us</span><span>Contact us</span>
    <svg width="15" height="15" viewBox="0 0 24 24"><circle cx="10" cy="10" r="7" fill="none" stroke="#1b1b1b" stroke-width="3"/><path d="M15 15l7 7" stroke="#1b1b1b" stroke-width="3"/></svg>
  </nav>
</header>

<section class="abs hero">
  <div class="hero-photo" role="img" aria-label="Photo of a smiling student holding a tablet in a library"></div>
  <svg class="hero-chevron" width="1087" height="490" viewBox="0 0 1087 490">
    <polygon points="470,0 720,0 1000,245 720,490 470,490" fill="#7ab51d" opacity=".85"/>
    <polygon points="720,0 880,0 1087,180 1087,300 880,490 720,490 1000,245" fill="#8cc52b" opacity=".6"/>
  </svg>
  <div class="hero-title">Vexmore Education</div>
  <p class="hero-text">Lorem ipsum dolor sit amet, consectetur adipiscing elit, sed do eiusmod tempor incididunt ut labore et</p>
  <div class="btn">GET STARTED
    <svg width="16" height="16" viewBox="0 0 16 16"><circle cx="8" cy="8" r="8" fill="#1b1b1b"/><path d="M5 8h6M8 5l3 3-3 3" stroke="#fbe82d" stroke-width="2" fill="none"/></svg>
  </div>
</section>

<div class="abs dots"><span class="on"></span><span></span><span></span><span></span></div>

<h1 class="abs welcome-title">Welcome to <b>Vexmore Education</b></h1>
<p class="abs welcome-text">Lorem ipsum dolor sit amet, consectetur adipiscing elit, sed do eiusmod tempor incididunt ut labore et dolore magna aliqua. Ut enim ad minim veniam, quis nostrud exercitation ullamco laboris nisi ut aliquip ex ea commodo consequat. Duis aute irure dolor in reprehenderit in voluptate velit esse cillum dolore eu fugiat nulla pariatur. Excepteur sint occaecat cupidatat non proident, sunt in culpa qui officia deserunt mollit anim id est laborum</p>
<div class="abs welcome-actions">
  <div class="btn btn-green">READ MORE</div>
  <div class="btn btn-yellow">CONTACT US</div>
</div>

<section class="abs services">
  <div class="gear-badge">
    <svg width="32" height="32" viewBox="0 0 24 24"><path fill="#7ab51d" d="M10 1h4l.6 3 2 .9 2.6-1.7 2.8 2.8-1.7 2.6.9 2 3 .6v4l-3 .6-.9 2 1.7 2.6-2.8 2.8-2.6-1.7-2 .9-.6 3h-4l-.6-3-2-.9-2.6 1.7-2.8-2.8 1.7-2.6-.9-2-3-.6v-4l3-.6.9-2L2.8 5.6l2.8-2.8 2.6 1.7 2-.9z"/><circle cx="12" cy="12" r="4" fill="#fff"/></svg>
  </div>
  <h2 class="services-title">Our <b>Services</b></h2>
  <p class="services-lead">Lorem ipsum dolor sit amet, consectetur adipiscing elit, sed do</p>
  <ul class="service-list">
    <li>Quasi Architecto</li>
    <li class="active">Voluptatem Accusantium</li>
    <li>Doloremque</li>
    <li>Voluptatem Accusantium</li>
    <li>Denouncing Pleasure</li>
  </ul>
  <article class="service-card">
    <div class="service-photo" role="img" aria-label="Photo of students studying together on a campus lawn"></div>
    <div class="service-icon">
      <svg width="34" height="24" viewBox="0 0 34 24"><rect x="1" y="1" width="32" height="20" rx="2" fill="none" stroke="#7ab51d" stroke-width="2"/><path d="M6 7h12M6 11h12M6 15h9" stroke="#7ab51d" stroke-width="2"/><circle cx="25" cy="9" r="3" fill="#7ab51d"/><path d="M20 17c1-3 9-3 10 0" stroke="#7ab51d" stroke-width="2" fill="none"/></svg>
    </div>
    <h3>voluptatem accusantium doloremque laudantium</h3>
    <p>Lorem ipsum dolor sit amet, consectetur adipiscing elit, sed do eiusmod tempor incididunt ut labore et dolore magna aliqua. Ut enim ad minim veniam, quis nostrud exercitation ullamco laboris nisi</p>
    <div class="more">READ MORE</div>
  </article>
</section>

<section class="abs feed" style="left:62px;width:344px">
  <div class="feed-head"><span class="sq"></span>Chirpnet Feed</div>
  <div class="post" style="top:54px">
    <div class="avatar" role="img" aria-label="Profile photo"></div>
    <div class="name">Dara Fenn<span>@vexmore</span></div>
    <p class="body">Lorem ipsum dolor sit amet, consectetur adipiscing elit, sed do eiusmod tempor incididunt <a>@labore</a> et dolore magna aliqua.</p>
    <div class="tag">#Chirpnet@vexmore</div>
    <div class="time">21m</div>
    <div class="dots3">•••</div>
    <div class="stats-v"><span class="heart">♥</span>3k<span>⇄</span>40<span>○</span>2</div>
  </div>
  <div class="post faded" style="top:214px">
    <div class="avatar" role="img" aria-label="Profile photo"></div>
    <div class="name">Mina Cole<span>@vexmore</span></div>
    <p class="body">Lorem ipsum dolor sit amet, consectetur adipiscing elit, sed do eiusmod tempor incididunt <a>@labore</a> et dolore magna aliqua.</p>
    <div class="tag">#Chirpnet@vexmore</div>
    <div class="time">21m</div>
    <div class="dots3">•••</div>
    <div class="stats-v"><span class="heart">♥</span>3k<span>⇄</span>40<span>○</span>2</div>
  </div>
</section>

<section class="abs feed" style="left:420px;width:345px">
  <div class="feed-head"><span class="sq"></span>WorkLoop</div>
  <div class="post" style="top:54px">
    <div class="avatar" role="img" aria-label="Profile photo"></div>
    <div class="name">Ollie Marsh<span style="margin-left:4px">@vexmore</span></div>
    <p class="body">Lorem <a>ipsum dolor</a> sit amet, consectetur adipiscing elit, <a>sed do eiusmod</a> tempor incididunt <a>@labore</a> et dolore magna aliqua.</p>
    <div class="tag" style="top:84px">#WorkLoop@vexmore</div>
    <div class="time" style="top:104px">1hr</div>
    <div class="stats-h" style="top:102px"><span class="heart">♥</span>3k<span>⇄ 40</span><span>○ 2</span></div>
    <div class="dots3">•••</div>
  </div>
  <div class="post faded" style="top:204px">
    <div class="avatar" role="img" aria-label="Profile photo"></div>
    <div class="name">Mina Cole<span style="margin-left:4px">@vexmore</span></div>
    <p class="body">Lorem <a>ipsum dolor</a> sit amet, consectetur adipiscing elit, <a>sed do eiusmod</a> tempor incididunt <a>@labore</a> et dolore magna aliqua.</p>
    <div class="tag" style="top:84px">#WorkLoop@vexmore</div>
    <div class="time" style="top:112px">21m</div>
    <div class="stats-h" style="top:110px"><span class="heart">♥</span>3k<span>⇄ 40</span><span>○ 2</span></div>
    <div class="dots3">•••</div>
  </div>
</section>

<section class="abs feed" style="left:780px;width:360px">
  <div class="feed-head">Latest Blog</div>
  <article class="blog" style="top:56px">
    <div class="blog-thumb" role="img" aria-label="Blog photo of a desk with paperwork" style="background:linear-gradient(135deg,#e6e9ee,#8795a8)"></div>
    <h4>Lorem ipsum dolor</h4>
    <p>Sed ut perspiciatis unde omnis iste natus error sit voluptatem accusantium</p>
    <div class="date"><i></i>Jan 13,2019</div>
  </article>
  <article class="blog" style="top:160px">
    <div class="blog-thumb" role="img" aria-label="Blog photo of a study scene in warm light" style="background:linear-gradient(135deg,#e8c28a,#7a5a3a)"></div>
    <h4>Lorem ipsum dolor</h4>
    <p>Sed ut perspiciatis unde omnis iste natus error sit voluptatem accusantium</p>
    <div class="date"><i></i>Jan 13,2019</div>
  </article>
  <article class="blog" style="top:263px">
    <div class="blog-thumb" role="img" aria-label="Blog photo of students at a laptop" style="background:linear-gradient(135deg,#a9c3d8,#3e5b72)"></div>
    <h4>Lorem ipsum dolor</h4>
    <p>Sed ut perspiciatis unde omnis iste natus error sit voluptatem accusantium</p>
    <div class="date"><i></i>Jan 13,2019</div>
  </article>
</section>

<footer class="abs footer">
  <div class="phone-badge">
    <svg width="22" height="22" viewBox="0 0 24 24"><path fill="#1e2433" d="M6.6 10.8a15 15 0 0 0 6.6 6.6l2.2-2.2c.3-.3.7-.4 1-.2 1.1.4 2.3.6 3.6.6.6 0 1 .4 1 1V20c0 .6-.4 1-1 1A17 17 0 0 1 3 4c0-.6.4-1 1-1h3.5c.6 0 1 .4 1 1 0 1.3.2 2.5.6 3.6.1.3 0 .7-.2 1z"/></svg>
  </div>
  <div class="social" aria-label="Social links">
    <span><i></i></span><span><i></i></span><span><i></i></span><span><i></i></span>
  </div>
  <div class="contact-line">
    <span>⚲ Ms. Alda Renfrew, 17 Wexbury Lane, Harwich, Essex, CO14 8PN</span><span>|</span>
    <span>✆ 0800512907</span><span>|</span>
    <span>✉ info@vexmore-edu.co.uk</span>
  </div>
  <div class="foot-nav">Home &nbsp;|&nbsp; Services &nbsp;|&nbsp; News &nbsp;|&nbsp; About us &nbsp;|&nbsp; Contact us</div>
  <div class="copyright">Copyrights © 2019,Vexmore Education. All rights reserved.</div>
</footer>

</body>
</html>
```